Namibia currently imports 60% of its food. Harvest Crest Oruva is an initiative which will assist Namibia to become self sustainable in terms of food production. We aim to do this through the development of 3 agricultural production zones which will include farming zones, local farmer assistance, processing and distribution of the final products. Please see our project overview attached.

```html
<!DOCTYPE html>
<html lang="en">
<head>
<meta charset="utf-8">
<title>Harvest Crest Oruva</title>
<link rel="stylesheet" href="https://fonts.googleapis.com/css2?family=Cinzel:wght@500;600&family=Outfit:wght@300;400;500;600&display=swap">
<style>
:root{
  --green:#0b5e2c;
  --green-dark:#084a22;
  --tan:#c4a27c;
  --tan-title:#c39a6b;
  --gray:#efefef;
  --cream:#f7f4ef;
  --ink:#222;
  --muted:#555;
  --white:#fff;
  --star:#f2a81d;
}
*{box-sizing:border-box;margin:0;padding:0}
html,body{width:1200px;height:4494px;overflow:hidden}
body{font-family:'Outfit',sans-serif;color:var(--ink);background:var(--white);position:relative}
section,header{position:relative;width:1200px}
.abs{position:absolute}

/* top bar */
.topbar{height:30px;background:var(--green);color:var(--white);font-size:13px}
.topbar .socials{left:141px;top:8px;display:flex;gap:9px}
.topbar .socials span{width:13px;height:13px;border-radius:50%;background:var(--white);display:block}
.topbar .contact{right:141px;top:6px;display:flex;gap:26px;align-items:center}
.topbar .contact span{display:flex;gap:6px;align-items:center}

/* nav */
.nav{height:76px;background:var(--white);border-bottom:1px solid #e6e6e6}
.brand{left:141px;top:22px;display:flex;align-items:center;gap:10px;color:var(--green);font-weight:500;font-size:24px;letter-spacing:.5px}
.brand i{width:14px;height:14px;border-radius:50%;background:var(--green);display:block}
.menu{left:412px;top:30px;display:flex;gap:25px;font-size:13.5px;color:var(--ink)}
.menu .active{color:var(--green);font-weight:500}
.btn{display:inline-flex;align-items:center;justify-content:center;gap:8px;background:var(--green);color:var(--white);font-size:13px;border-radius:4px}
.nav .btn{right:141px;top:18px;width:126px;height:40px}

/* hero */
.hero{height:529px;overflow:hidden}
.hero .photo{inset:0;background:linear-gradient(90deg,#2b3a20 0%,#4f5b30 35%,#8a7a4a 62%,#a79160 78%,#5d6e35 100%)}
.hero .shade{inset:0;background:linear-gradient(90deg,rgba(0,0,0,.35),rgba(0,0,0,0) 60%)}
.hero h1{left:145px;top:203px;font-family:'Cinzel',serif;font-weight:500;font-size:53px;line-height:56px;letter-spacing:2px;color:var(--white)}
.hero p{left:141px;top:438px;font-size:15px;color:var(--white)}
.hero .btn{left:141px;top:377px;width:204px;height:38px}

/* mission */
.mission{height:338px;background:var(--gray)}
.mission .cards{left:141px;top:57px;width:918px;height:224px;background:var(--white);display:grid;grid-template-columns:repeat(3,1fr)}
.mission .card{padding:36px 30px 0 31px;border-right:1px solid #e5e5e5}
.mission .card:last-child{border-right:0}
.mission h3{font-family:'Cinzel',serif;font-weight:500;font-size:17px;letter-spacing:1px;margin:18px 0 10px}
.mission p{font-size:12.5px;line-height:22px;color:var(--muted)}

/* about */
.about{height:527px}
.ph{background:linear-gradient(135deg,#c99a3a,#6d6a2c 60%,#2f4a20)}
.about .img1{left:180px;top:75px;width:270px;height:355px}
.about .img2{left:357px;top:310px;width:178px;height:168px;background:linear-gradient(135deg,#5e7b3a,#2e4e20);border:6px solid var(--white)}
.about .play{left:418px;top:162px;width:64px;height:64px;border-radius:50%;border:2px solid var(--green);display:flex;align-items:center;justify-content:center;background:rgba(255,255,255,.25)}
.about .play span{width:44px;height:44px;border-radius:50%;background:var(--green);display:flex;align-items:center;justify-content:center}
.about .call{left:128px;top:292px;width:167px;height:69px;background:var(--white);box-shadow:0 4px 18px rgba(0,0,0,.12);display:flex;align-items:center;gap:10px;padding-left:14px}
.about .call .ico{width:36px;height:36px;border-radius:50%;background:var(--green);display:flex;align-items:center;justify-content:center}
.about .call small{display:block;font-size:10px}
.about .call b{font-weight:500;font-size:13.5px}
.about .text{left:612px;top:97px;width:438px}
.title-tan{color:var(--tan-title);font-weight:500}
.about h2{font-size:27px;padding-bottom:8px;border-bottom:2px solid var(--green);display:inline-block;margin-bottom:24px}
.about p{font-size:11.5px;line-height:22.5px;color:#333;margin-bottom:14px}
.about .btn{left:612px;top:425px;width:137px;height:38px;border-radius:20px}

/* projects */
.projects{height:1017px}
.projects .band{left:0;top:441px;width:1200px;height:576px;background:var(--tan)}
.sec-title{position:absolute;left:0;width:1200px;text-align:center;font-size:27px}
.sec-title:after{content:"";display:block;width:60px;height:2px;background:var(--green);margin:10px auto 0}
.projects .cards{left:141px;top:132px;display:flex;gap:24px}
.pcard{width:290px;height:388px;background:var(--white);padding:14px;box-shadow:0 2px 14px rgba(0,0,0,.07)}
.pcard .ph{height:202px;margin-bottom:20px}
.pcard h3{font-size:14.5px;font-weight:600;padding:0 4px;margin-bottom:13px}
.pcard p{font-size:11.5px;line-height:20.5px;color:#444;padding:0 4px;height:64px}
.readmore{display:flex;align-items:center;gap:8px;color:var(--green);font-size:12.5px;font-weight:600;text-decoration:underline;margin:8px 4px 0}
.readmore span{width:21px;height:21px;border-radius:50%;background:var(--green);display:flex;align-items:center;justify-content:center}
.projects .map{left:366px;top:544px;width:468px;height:446px;background:radial-gradient(ellipse at 45% 45%,#f3ebe0 0%,#e2d0b8 45%,rgba(196,162,124,0) 72%)}
.projects .pins{left:872px;top:868px;color:var(--white);font-size:12.5px;display:flex;flex-direction:column;gap:21px}
.projects .pins div{display:flex;align-items:center;gap:14px}

/* testimonials */
.testimonials{height:513px}
.tcard{position:absolute;top:195px;width:446px;height:218px;background:var(--cream);padding:50px 36px 0;text-align:center}
.tcard .quote{position:absolute;left:22px;top:-14px;font-family:Georgia,serif;font-size:80px;line-height:80px;color:var(--green);font-weight:700}
.tcard p{font-size:10.5px;line-height:20px;color:#333}
.tcard .who{display:flex;align-items:center;justify-content:center;gap:14px;margin-top:22px;text-align:left}
.tcard .avatar{width:56px;height:56px;border-radius:50%;background:linear-gradient(135deg,#d6c4aa,#8c7356)}
.tcard b{font-size:13px;font-weight:500}
.stars{color:var(--star);font-size:16px;letter-spacing:3px}
.testimonials .arrows{left:540px;top:444px;display:flex;gap:40px}

/* stats */
.stats{height:280px}
.stats .box{left:141px;top:29px;width:918px;height:223px;background:var(--green);overflow:hidden}
.stats .leaf{left:300px;top:30px;width:300px;height:220px;border-radius:0 100% 0 100%;background:rgba(255,255,255,.05)}
.stat{position:absolute;top:62px;color:var(--white)}
.stat b{display:block;font-size:31px;font-weight:600;margin-bottom:10px}
.stat span{font-size:11.5px;line-height:20px;display:block;width:110px}

/* news */
.news{height:570px}
.news .cards{left:141px;top:154px;display:flex;gap:24px}
.ncard{width:290px;height:361px;background:var(--white);box-shadow:0 2px 14px rgba(0,0,0,.07);position:relative}
.ncard .ph{height:195px}
.ncard .body{padding:20px 21px}
.ncard small{font-size:11px;color:var(--tan-title)}
.ncard h3{font-size:14px;font-weight:500;line-height:24px;margin:6px 0 14px}
.ncard .readmore{margin:0;gap:6px}
.ncard.feature .ph{position:absolute;inset:0;height:auto;background:linear-gradient(180deg,#a9b59a 0%,#6d6a4a 45%,#2a2418 100%)}
.ncard.feature .body{position:absolute;left:0;bottom:0;color:var(--white)}
.ncard.feature small,.ncard.feature .readmore{color:var(--white)}

/* newsletter */
.newsletter{height:299px}
.newsletter h2{top:51px;line-height:42px}
.newsletter .form{left:382px;top:170px;width:432px;height:42px;border-radius:21px;background:#f0f0f0;display:flex;align-items:center;justify-content:space-between;padding:0 3px 0 18px;font-size:12px;color:#666}
.newsletter .btn{width:126px;height:36px;border-radius:18px;font-weight:500}

/* footer */
.footer{height:315px;background:var(--green);color:var(--white)}
.footer .brand{left:141px;top:82px;color:var(--white);font-size:26px}
.footer .brand i{background:var(--white)}
.fcol{position:absolute;top:66px;font-size:12px}
.fcol h4{color:var(--tan);font-weight:500;font-size:14px;margin-bottom:16px}
.fcol li{list-style:none;margin-bottom:14px}
.fcol .row{display:flex;gap:10px;margin-bottom:14px;line-height:19px}
.footer .rule{left:141px;top:256px;width:918px;height:1px;background:rgba(255,255,255,.25)}
.footer .copy{left:141px;top:279px;font-size:11.5px}
.footer .social{right:141px;top:272px;display:flex;gap:10px}
.footer .social span{width:27px;height:27px;border-radius:50%;background:var(--tan);display:block}
</style>
</head>
<body>

<header class="topbar">
  <div class="abs socials"><span></span><span></span><span></span><span></span></div>
  <div class="abs contact">
    <span><svg width="14" height="11" viewBox="0 0 14 11" fill="none" stroke="#fff"><rect x=".5" y=".5" width="13" height="10" rx="1"/><path d="M1 1l6 5 6-5"/></svg>info@harvestcrestoruva.com</span>
    <span><svg width="12" height="12" viewBox="0 0 24 24" fill="none" stroke="#fff" stroke-width="2"><path d="M22 16.9v3a2 2 0 0 1-2.2 2 19.8 19.8 0 0 1-8.6-3.1 19.5 19.5 0 0 1-6-6A19.8 19.8 0 0 1 2.1 4.2 2 2 0 0 1 4.1 2h3a2 2 0 0 1 2 1.7c.1 1 .4 1.9.7 2.8a2 2 0 0 1-.5 2.1L8 9.9a16 16 0 0 0 6 6l1.3-1.3a2 2 0 0 1 2.1-.4c.9.3 1.8.6 2.8.7a2 2 0 0 1 1.7 2z"/></svg>123-456-7890</span>
  </div>
</header>

<header class="nav">
  <div class="abs brand"><i></i>Harvest Crest Oruva</div>
  <nav class="abs menu"><span class="active">Home</span><span>About Us</span><span>Our Projects</span><span>Farmer Resources</span><span>News &amp; Updates</span></nav>
  <span class="abs btn">Contact Us</span>
</header>

<section class="hero">
  <div class="abs photo" role="img" aria-label="Two smiling women tending leafy crops in a green field"></div>
  <div class="abs shade"></div>
  <h1 class="abs">Empowering<br>Namibia to<br>Achieve Food<br>Independence</h1>
  <p class="abs" style="top:438px">Reducing imports by fostering local agricultural production</p>
  <span class="abs btn" style="top:483px">Learn About Our Projects</span>
</section>

<section class="mission">
  <div class="abs cards">
    <div class="card">
      <svg width="42" height="42" viewBox="0 0 42 42" fill="none" stroke="#222" stroke-width="1.5"><circle cx="20" cy="22" r="17"/><circle cx="20" cy="22" r="11"/><circle cx="20" cy="22" r="5"/><path d="M20 22L36 6M31 6h5v5"/></svg>
      <h3>Our Mission</h3>
      <p>Lorem ipsum dolor sit amet, dolor ex consectetur adipiscing elit, sed do ut eiusmod tempor.</p>
    </div>
    <div class="card">
      <svg width="42" height="42" viewBox="0 0 42 42" fill="none" stroke="#222" stroke-width="1.5"><circle cx="21" cy="10" r="7"/><circle cx="21" cy="10" r="3"/><circle cx="11" cy="24" r="4"/><circle cx="21" cy="22" r="4"/><circle cx="31" cy="24" r="4"/><path d="M4 38c0-5 3-8 7-8s7 3 7 8M14 38c0-6 3-10 7-10s7 4 7 10M24 38c0-5 3-8 7-8s7 3 7 8"/></svg>
      <h3>Our Vision</h3>
      <p>Lorem ipsum dolor sit amet, dolor ex consectetur adipiscing elit, sed do ut eiusmod tempor.</p>
    </div>
    <div class="card">
      <svg width="42" height="42" viewBox="0 0 42 42" fill="none" stroke="#222" stroke-width="1.5"><circle cx="12" cy="6" r="3"/><circle cx="21" cy="4" r="3"/><circle cx="30" cy="6" r="3"/><circle cx="21" cy="20" r="5"/><path d="M12 38c0-6 4-10 9-10s9 4 9 10M4 16l5 14h4M38 16l-5 14h-4"/></svg>
      <h3>Our Values</h3>
      <p>Lorem ipsum dolor sit amet, dolor ex consectetur adipiscing elit, sed do ut eiusmod tempor.</p>
    </div>
  </div>
</section>

<section class="about">
  <div class="abs ph img1" role="img" aria-label="Farmer walking through a crop field at sunset"></div>
  <div class="abs img2" role="img" aria-label="Woman holding a crate of freshly harvested cucumbers"></div>
  <div class="abs play"><span><svg width="14" height="16" viewBox="0 0 14 16"><path d="M1 1l12 7-12 7z" fill="#fff"/></svg></span></div>
  <div class="abs call">
    <div class="ico"><svg width="16" height="16" viewBox="0 0 24 24" fill="#fff"><path d="M22 16.9v3a2 2 0 0 1-2.2 2 19.8 19.8 0 0 1-8.6-3.1 19.5 19.5 0 0 1-6-6A19.8 19.8 0 0 1 2.1 4.2 2 2 0 0 1 4.1 2h3a2 2 0 0 1 2 1.7c.1 1 .4 1.9.7 2.8a2 2 0 0 1-.5 2.1L8 9.9a16 16 0 0 0 6 6l1.3-1.3a2 2 0 0 1 2.1-.4c.9.3 1.8.6 2.8.7a2 2 0 0 1 1.7 2z"/></svg></div>
    <div><small>Contact Us</small><b>123-456-7890</b></div>
  </div>
  <div class="abs text">
    <h2 class="title-tan">About Us</h2>
    <p>Namibia is a young democracy in Sub-Saharan Africa with a population of approximately 2.5 Million people. The country's agricultural sector has been slow to keep up with the increasing population. As a consequence, approximately 60% of the food required to feed the nation is imported. The elevated cost of these imported foods means a large proportion of the population consume food with low nutritional value.</p>
    <p>Despite vast tracts of available arable land and abundant water resources (both above and below ground), the agricultural sector has struggled to capitalise. This is largely due to a lack of investment, technical knowledge and available technologies.</p>
  </div>
  <span class="abs btn">Learn More <svg width="18" height="10" viewBox="0 0 18 10" fill="none" stroke="#fff" stroke-width="1.5"><path d="M0 5h16M12 1l4 4-4 4"/></svg></span>
</section>

<section class="projects">
  <div class="abs band"></div>
  <h2 class="sec-title title-tan" style="top:54px">Our Projects</h2>
  <div class="abs cards">
    <article class="pcard">
      <div class="ph" role="img" aria-label="Farmer carrying crates across rows of leafy vegetables" style="background:linear-gradient(160deg,#a4a27a,#4f6b2c 55%,#2c4419)"></div>
      <h3>Farming Zones</h3>
      <p>The country's agricultural sector has been slow to keep up with the increasing population.</p>
      <div class="readmore">Read More <span><svg width="9" height="9" viewBox="0 0 9 9" fill="none" stroke="#fff" stroke-width="1.5"><path d="M1 8l7-7M3 1h5v5"/></svg></span></div>
    </article>
    <article class="pcard">
      <div class="ph" role="img" aria-label="Group of farmers planting seedlings in red soil" style="background:linear-gradient(160deg,#4c6a2a,#8b6a3c 55%,#a5693f)"></div>
      <h3>Local Farmer Assistance</h3>
      <p>Despite vast tracts of available arable land and abundant water resources (both above and below ground)</p>
      <div class="readmore">Read More <span><svg width="9" height="9" viewBox="0 0 9 9" fill="none" stroke="#fff" stroke-width="1.5"><path d="M1 8l7-7M3 1h5v5"/></svg></span></div>
    </article>
    <article class="pcard">
      <div class="ph" role="img" aria-label="Workers sorting fresh greens inside a greenhouse" style="background:linear-gradient(160deg,#dfe6e3,#8fa89a 45%,#3f6a2f)"></div>
      <h3>Processing and Distribution</h3>
      <p>Each of the allocated production zones will be furnished with handling, processing and milling facilities for all crops produced</p>
      <div class="readmore">Read More <span><svg width="9" height="9" viewBox="0 0 9 9" fill="none" stroke="#fff" stroke-width="1.5"><path d="M1 8l7-7M3 1h5v5"/></svg></span></div>
    </article>
  </div>
  <div class="abs map" role="img" aria-label="Dotted map of Namibia with markers at the three production zones"></div>
  <div class="abs pins">
    <div><svg width="20" height="24" viewBox="0 0 20 24" fill="none" stroke="#fff" stroke-width="1.5"><path d="M10 22s7-7 7-12a7 7 0 0 0-14 0c0 5 7 12 7 12z"/><circle cx="10" cy="10" r="2.5"/><ellipse cx="10" cy="22" rx="7" ry="1.5"/></svg>Otavi Region - Central Namibia</div>
    <div><svg width="20" height="24" viewBox="0 0 20 24" fill="none" stroke="#fff" stroke-width="1.5"><path d="M10 22s7-7 7-12a7 7 0 0 0-14 0c0 5 7 12 7 12z"/><circle cx="10" cy="10" r="2.5"/><ellipse cx="10" cy="22" rx="7" ry="1.5"/></svg>Kavango Region - North Namibia</div>
    <div><svg width="20" height="24" viewBox="0 0 20 24" fill="none" stroke="#fff" stroke-width="1.5"><path d="M10 22s7-7 7-12a7 7 0 0 0-14 0c0 5 7 12 7 12z"/><circle cx="10" cy="10" r="2.5"/><ellipse cx="10" cy="22" rx="7" ry="1.5"/></svg>Neckartal Dam - South Namibia</div>
  </div>
</section>

<section class="testimonials">
  <h2 class="sec-title title-tan" style="top:88px">Our Happy Customers</h2>
  <div class="tcard" style="left:136px">
    <span class="quote">&ldquo;</span>
    <p>It is a long established fact that a reader will be distracted by the readable content of a page when looking at its layout. The point of using Lorem Ipsum is that it has a more-or-less normal distribution of letters, as opposed to using 'Content here, content here', making it look like readable English.</p>
    <div class="who"><div class="avatar" role="img" aria-label="Customer portrait"></div><div><b>Tomas Hale</b><div class="stars">★★★★★</div></div></div>
  </div>
  <div class="tcard" style="left:607px">
    <span class="quote">&ldquo;</span>
    <p>There are many variations of passages of Lorem Ipsum available, but the majority have suffered alteration in some form, by injected humour, or randomised words which don't look even slightly believable. If you are going to use a passage of Lorem Ipsum</p>
    <div class="who"><div class="avatar" role="img" aria-label="Customer portrait"></div><div><b>Ari Lindqvist</b><div class="stars">★★★★★</div></div></div>
  </div>
  <div class="abs arrows">
    <svg width="30" height="14" viewBox="0 0 30 14" fill="none" stroke="#0b5e2c" stroke-width="2"><path d="M30 7H2M8 1L2 7l6 6"/></svg>
    <svg width="30" height="14" viewBox="0 0 30 14" fill="none" stroke="#0b5e2c" stroke-width="2"><path d="M0 7h28M22 1l6 6-6 6"/></svg>
  </div>
</section>

<section class="stats">
  <div class="abs box">
    <div class="abs leaf"></div>
    <div class="stat" style="left:96px"><b>95%</b><span>Hectares Of Land Cultivated</span></div>
    <div class="stat" style="left:299px"><b>3000+</b><span>Farmers Assisted</span></div>
    <div class="stat" style="left:501px"><b>100+</b><span>Farmers In The Farm</span></div>
    <div class="stat" style="left:705px"><b>80%</b><span>Reduction In Food Imports</span></div>
  </div>
</section>

<section class="news">
  <h2 class="sec-title title-tan" style="top:58px">Latest News And Updates</h2>
  <div class="abs cards">
    <article class="ncard feature">
      <div class="ph" role="img" aria-label="Woman carrying a basket of vegetables in a greenhouse tunnel"></div>
      <div class="body">
        <small>October 6, 2023</small>
        <h3>Despite vast tracts of available arable land and abundant water resources</h3>
        <div class="readmore">Read More <svg width="14" height="8" viewBox="0 0 14 8" fill="none" stroke="currentColor" stroke-width="1.4"><path d="M0 4h12M9 1l3 3-3 3"/></svg></div>
      </div>
    </article>
    <article class="ncard">
      <div class="ph" role="img" aria-label="Rows of green crops under a bright sky" style="background:linear-gradient(180deg,#9cc6e6 0%,#d9e4d0 35%,#5f8a2f 60%,#3a5d1d 100%)"></div>
      <div class="body">
        <small>September 19, 2023</small>
        <h3>Harvest Crest Oruva" initiative to be a vector for an accelerated change</h3>
        <div class="readmore">Read More <svg width="14" height="8" viewBox="0 0 14 8" fill="none" stroke="currentColor" stroke-width="1.4"><path d="M0 4h12M9 1l3 3-3 3"/></svg></div>
      </div>
    </article>
    <article class="ncard">
      <div class="ph" role="img" aria-label="Woman kneeling to tend seedlings in a greenhouse" style="background:linear-gradient(180deg,#dfe3df 0%,#9aa48a 45%,#6d5a3c 100%)"></div>
      <div class="body">
        <small>November 8, 2023</small>
        <h3>Harvest Crest Oruva program would be to establish 3 distinct food production</h3>
        <div class="readmore">Read More <svg width="14" height="8" viewBox="0 0 14 8" fill="none" stroke="currentColor" stroke-width="1.4"><path d="M0 4h12M9 1l3 3-3 3"/></svg></div>
      </div>
    </article>
  </div>
</section>

<section class="newsletter">
  <h2 class="sec-title title-tan">Subscribe To A Newsletter For<br>Regular Updates</h2>
  <div class="abs form"><span>Enter your email</span><span class="btn">Subscribe <svg width="18" height="10" viewBox="0 0 18 10" fill="none" stroke="#fff" stroke-width="1.5"><path d="M0 5h16M12 1l4 4-4 4"/></svg></span></div>
</section>

<footer class="footer" style="position:relative;width:1200px">
  <div class="abs brand"><i></i>Harvest Crest Oruva</div>
  <div class="fcol" style="left:440px"><h4>Quick Links</h4><ul><li>About Us</li><li>Our Projects</li><li>Farmer Resources</li><li>News &amp; Updates</li></ul></div>
  <div class="fcol" style="left:649px"><h4>Resources</h4><ul><li>Privacy Policy</li><li>Terms Of Service</li></ul></div>
  <div class="fcol" style="left:853px">
    <h4>Contact Info</h4>
    <div class="row"><svg width="16" height="18" viewBox="0 0 20 24" fill="none" stroke="#c4a27c" stroke-width="2"><path d="M10 22s7-7 7-12a7 7 0 0 0-14 0c0 5 7 12 7 12z"/><circle cx="10" cy="10" r="2.5"/></svg><span>123, Lorem ipsum dolor site<br>#123, Lorem ipsum 123456</span></div>
    <div class="row"><svg width="16" height="13" viewBox="0 0 14 11" fill="#c4a27c"><rect width="14" height="11" rx="1"/><path d="M1 1l6 5 6-5" stroke="#0b5e2c" fill="none"/></svg><span>info@harvestcrestoruva.com</span></div>
    <div class="row"><svg width="15" height="15" viewBox="0 0 24 24" fill="#c4a27c"><path d="M22 16.9v3a2 2 0 0 1-2.2 2 19.8 19.8 0 0 1-8.6-3.1 19.5 19.5 0 0 1-6-6A19.8 19.8 0 0 1 2.1 4.2 2 2 0 0 1 4.1 2h3a2 2 0 0 1 2 1.7c.1 1 .4 1.9.7 2.8a2 2 0 0 1-.5 2.1L8 9.9a16 16 0 0 0 6 6l1.3-1.3a2 2 0 0 1 2.1-.4c.9.3 1.8.6 2.8.7a2 2 0 0 1 1.7 2z"/></svg><span>123-456-7890</span></div>
  </div>
  <div class="abs rule"></div>
  <div class="abs copy">© 2024 Harvest Crest Oruva. All rights reserved.</div>
  <div class="abs social"><span></span><span></span><span></span><span></span></div>
</footer>

</body>
</html>
```